Updated ebook fantasy cover with feathered dragon and twisted tail

Ebook designs are a specific type of layout. They must be at least partially legible at thumbnail size on Amazon, and interesting enough to draw the eye of a modern fantasy book reader.

Before you begin, I have an extensive collection of my likes and a few critiques of other covers on a pintrest board.
http://www.moodvault.example/vossmarlowe/brindle-cover-ideas/

Let me also say that the story is not scary, it is set in a gorgeous natural environment on planet earth, and I do not want monsterous dragons. The dragon is the good guy, he talks, and his best friend is a fairy. Think cuddly.

As for colors, I am trying to attract young women. They are drawn to beautiful images like those you see on my pintrest board. To help, I have chosen some colors below, but you don't have to use them all. As for the pop of color. Use your design instincts.

The following text must fit on the cover.
Brindle A Wyrm Chronicle (title- should be readable at thumbnail size)
Tales of the Meridian (series title)
Delphine Voss Marlowe (author)

The hero of the book and the subject of the cover is a dragon with:
*A long corkscrew like tail
*Feathered wings (black with white lower edges)
*Black feathers covering his chest (over lungs) but the rest is scales. (scales need not be overly obvious.
*A large, indigo (not Aqua) blue crest of feathers like a cockatiel (see attached photo)
*A thin line of feathers snaking up the back of the neck*
*Workable arms (no T Rex issues)
*An intelligent and even gentle appearance
*No large horns
*Body is black with highlights that can be blue or whatever color works best in the setting
*Striking blue eyes that appear kind rather than fierce

This dragon should be what you imagine as a precursor to the birds of today. You will see what I mean on my pintrest board, or ask questions. I prefer focused covers with a warm color palette NO MONOTONE or washed out layouts, please. The entire dragon does not need to appear. The winning design will lean toward whimsy, but not juvenile.

If you are looking for a background, consider
*a light filled forest
*a beach at sunset (but not in the water)
*near a waterfall
*near a lake
*a mountain peak
*or a simple, light colored, elegantly textured background
You may have other ideas.

Design should be a minimum of 300 dpi at 6 x 9 inches

I feel that I may have confused you.
Elegant
Beautiful
Inviting
Charming
Sweet
These are words that should describe the cover.

You may use either illustration, stock photos, or any combination.

The topography should be striking, easy to read and creative.

I expect a controlled and thoughtfully placed pop of color to draw the eye to the title or the dragon.

If you are looking for a way to introduce color, consider adding
* the northern lights (Aurora)
*colorful gemstones or crystals
*a colorful band of ripped tapestry, but the dragon should not seem to be in possession of the tapestry.
Another idea is below.

Extra consideration will be given to designs that are large enough to extend onto the spine of a 6 x 9 book for a 300 page createspace book. Ask for exact dimensions if interested.

Two more elements can be considered for addition.
*A Cairn (think a pile of rocks)
*A small, beautiful wingless fairy like creature (they are best friends) I prefer that she not be represented in her complete form, but perhaps her hand reaching out to the dragon as her sleeve drapes in some pop of color. She has long, wavy brown hair. You could show her from the back, perhaps dressed in a cloak.

This is the blurb:
"Every dragon dreams of entering the Cairn—but not as a murder victim.

Quillon, the dragon with the twisted tail, is summoned home to the lair by a sweet and familiar voice. “Bring the trollkin known as Moss to me or all will be lost,” she beckons. Except, Quillon has already fulfilled his destiny, and he has no reason to risk his life, yet again. Still, nobody denies an Elemental, and certainly not a dragon of the Cobalt kin. But is she calling him home to die, or will he expose the brutal killer before he becomes the next victim?

Brindle: A Wyrm Chronicle penetrates the world of dragons, a society filled with smoke and lies where honorable wishes are warped by vague memories and unfathomable greed. "

This will be a relaunch and it is part of a trilogy so I am very interested in working with the same designer for all three. The first book features a female troll and the third the creature that you can think of as a beautiful fairy without wings. So this one project could well lead to three.

I have added a cairn photo that I purchased from Istock and an idea of what I mean by a twisted tail, but it should fit the dragon and not be as thin as a snake.

To see the cover as it is today: Hint, I do like my current topography, but think it could be even better.
http://www.bookmart.example/Brindle-Wyrm-Chronicle-Tales-Meridian-ebook/dp/X00Q7KZWPA/ref=sr_1_2?ie=UTF8&qid=1408362392&sr=8-2&keywords=voss+marlowe

After reviewing more of the amazing designs created by the designers on this site, I have decided to both guarantee and increase the budget for my project. I look forward to seeing the designs from the designers who have already accepted, and any others who may have been on the fence about accepting the challenge. I feel confident that one of you will create a design that will whack me to my knees, and for that, you will deserve a larger reward. If you are interested, start at my pintrest board for my likes and dislikes. http://www.moodvault.example/vossmarlowe/brindle-cover-ideas/

Reason: My updated (and clarified) brief drew more interested designers, and to to be fair, I have decided to extend the deadline by a few days. I am very interested to see all your designs so take more time if you need it. I am offering detailed feedback to anyone who requests it.

Target Market(s)

Young adult, primarily female, 15+. A reader of fantasy. The dragon is the primary element.

Industry/Entity Type

Environment

Font styles to use
Other font styles liked:
• I like Trajon Pro, but perhaps add script to add some elegance i

Colors
fee18a
fcf9ce
0255a3
ffc214
faa54b
9bcb3c
f68d4d

Requirements
Must have
• some or all of the dragon described above
a pop of color
professional font treatment
Interesting at thumbnail size as seen on Amazon
Nice to have
• the fairy like creature described above in a loving pose with the dragon
the rock pile,
I am not telling you what color to use, but I don't like pastels, I do like warm colors or greens
Should not have
• cartoonish features.
unreadable font.
Monotone color scheme. large blocks of color that seem to exist only to hold the text.
Setting that could not exist on this planet
Excessive fire

```html
<!DOCTYPE html>
<html lang="en">
<head>
<meta charset="utf-8">
<title>Brindle A Wyrm Chronicle — Cover Wrap</title>
<link rel="stylesheet" href="https://fonts.googleapis.com/css2?family=Bebas+Neue&family=Oswald:wght@300;400;500&display=swap">
<style>
  :root {
    --stage: #e6e6e6;
    --cover-black: #0b0b0c;
    --cover-ink: #141414;
    --title-white: #efefef;
    --muted-grey: #8e8e8e;
    --body-grey: #9a9a9a;
    --box-grey: #262626;
    --box-label: #8a8a8a;
    --ember: #e07a1f;
    --flame: #f3a23a;
    --plum: #4a1d3c;
    --scale-blue: #8fd0e6;
    --deep-blue: #2b5e7d;
  }
  * { box-sizing: border-box; margin: 0; padding: 0; }
  html, body {
    width: 1200px; height: 800px; overflow: hidden;
    background: var(--stage);
  }
  .wrap {
    position: absolute; left: 170px; top: 100px;
    width: 860px; height: 600px;
    display: flex;
    box-shadow: 0 10px 30px rgba(0,0,0,.25);
  }

  /* Back cover */
  .back-cover {
    position: relative; width: 400px; height: 600px;
    background: var(--cover-black);
    padding: 26px 34px 0;
    overflow: hidden;
  }
  .back-cover__glow {
    position: absolute; right: 0; bottom: 0; width: 40px; height: 330px;
    background: linear-gradient(270deg, rgba(224,122,31,.55), rgba(74,29,60,.25) 50%, transparent);
  }
  .back-series {
    font: 400 15px/1 'Oswald', sans-serif; letter-spacing: .06em;
    color: var(--muted-grey); text-transform: uppercase;
  }
  .back-title {
    font: 400 38px/1 'Bebas Neue', sans-serif; letter-spacing: .01em;
    color: var(--muted-grey); text-transform: uppercase; margin-top: 4px;
  }
  .back-author {
    font: 400 12px/1 'Oswald', sans-serif; letter-spacing: .05em;
    color: var(--muted-grey); text-transform: uppercase;
    text-align: center; margin-top: 5px; width: 300px;
  }
  .back-blurb {
    margin-top: 24px;
    font: 400 11.4px/1.27 'Oswald', sans-serif;
    color: var(--body-grey); text-align: justify; letter-spacing: .02em;
    height: 360px; overflow: hidden;
  }
  .back-boxes {
    position: absolute; left: 34px; right: 34px; bottom: 38px;
    display: flex; justify-content: space-between;
  }
  .placeholder-box {
    width: 100px; height: 58px; background: var(--box-grey);
    display: flex; align-items: center; justify-content: center;
    font: 500 11px/1 'Oswald', sans-serif; letter-spacing: .08em;
    color: var(--box-label); text-transform: uppercase;
  }

  /* Spine */
  .spine {
    position: relative; width: 60px; height: 600px;
    background: linear-gradient(90deg, #0e0e0f, #151515 60%, #0b0b0c);
    overflow: hidden;
  }
  .spine__glow {
    position: absolute; left: 0; right: 0; bottom: 0; height: 140px;
    background: linear-gradient(0deg, rgba(224,122,31,.7), rgba(74,29,60,.35) 60%, transparent);
  }
  .spine-text {
    position: absolute; left: 50%; top: 22px;
    transform-origin: 0 0; transform: rotate(90deg) translateY(-50%);
    white-space: nowrap; display: flex; align-items: baseline; gap: 18px;
  }
  .spine-title {
    font: 400 32px/1 'Bebas Neue', sans-serif; letter-spacing: .06em;
    color: #cfcfcf; text-transform: uppercase;
  }
  .spine-author {
    font: 400 10px/1 'Oswald', sans-serif; letter-spacing: .06em;
    color: #bdbdbd; text-transform: uppercase;
  }

  /* Front cover */
  .front-cover {
    position: relative; width: 400px; height: 600px;
    background: var(--cover-ink); overflow: hidden;
  }
  .front-art {
    position: absolute; inset: 0;
    background:
      radial-gradient(ellipse 90px 150px at 320px 250px, rgba(160,210,230,.85), rgba(60,110,140,.3) 70%, transparent),
      radial-gradient(ellipse 150px 170px at 355px 520px, rgba(150,205,228,.95), rgba(43,94,125,.55) 65%, transparent),
      radial-gradient(ellipse 190px 260px at 320px 170px, rgba(243,162,58,.75), rgba(224,122,31,.35) 55%, transparent),
      radial-gradient(ellipse 120px 200px at 230px 360px, rgba(224,122,31,.55), transparent 70%),
      radial-gradient(ellipse 240px 320px at 280px 80px, rgba(74,29,60,.9), transparent 75%),
      radial-gradient(ellipse 120px 140px at 20px 560px, rgba(224,122,31,.45), transparent 75%),
      linear-gradient(90deg, var(--cover-ink) 20%, #1a0f17 60%, #2a1424);
  }
  .front-type {
    position: absolute; left: 30px; top: 124px; width: 230px;
    text-align: center; color: var(--title-white);
  }
  .front-series {
    font: 400 17px/1 'Oswald', sans-serif; letter-spacing: .08em;
    text-transform: uppercase; white-space: nowrap;
  }
  .front-title {
    font: 400 82px/.9 'Bebas Neue', sans-serif; letter-spacing: .01em;
    text-transform: uppercase; margin-top: 26px;
  }
  .front-title__line { display: block; }
  .front-connector {
    display: flex; align-items: center; justify-content: center;
    gap: 4px; margin: 4px 0 0;
  }
  .wings-ornament {
    width: 150px; height: 34px; position: absolute; left: 40px;
    background: radial-gradient(ellipse at center, rgba(240,240,240,.55), rgba(240,240,240,.08) 70%, transparent);
  }
  .front-connector__a {
    position: relative;
    font: 400 40px/1 'Bebas Neue', sans-serif; text-transform: uppercase;
  }
  .front-author {
    font: 400 22px/1 'Oswald', sans-serif; letter-spacing: .02em;
    text-transform: uppercase; margin-top: 14px; white-space: nowrap;
  }
</style>
</head>
<body>
  <main class="wrap">
    <section class="back-cover">
      <div class="back-cover__glow"></div>
      <p class="back-series">Tales of the Meridian</p>
      <h2 class="back-title">Brindle A Wyrm Chronicle</h2>
      <p class="back-author">Delphine Voss Marlowe</p>
      <p class="back-blurb">
        Lorem ipsum dolor sit amet, consectetur adipisicing elit, sed do eiusmod tempor incididunt ut labore et dolore magna aliqua. Ut enim ad minim veniam, quis nostrud exercitation.
        Lorem ipsum dolor sit amet, consectetur adipisicing elit, sed do eiusmod tempor incididunt ut labore et dolore magna aliqua. Ut enim ad minim veniam, quis nostrud exercitation.
        Lorem ipsum dolor sit amet, consectetur adipisicing elit, sed do eiusmod tempor incididunt ut labore et dolore magna aliqua. Ut enim ad minim veniam, quis nostrud exercitation.
        Lorem ipsum dolor sit amet, consectetur adipisicing elit, sed do eiusmod tempor incididunt ut labore et dolore magna aliqua. Ut enim ad minim veniam, quis nostrud exercitation.
        Lorem ipsum dolor sit amet, consectetur adipisicing elit, sed do eiusmod tempor incididunt ut labore et dolore magna aliqua. Ut enim ad minim veniam, quis nostrud exercitation.
        Lorem ipsum dolor sit amet, consectetur adipisicing elit, sed do eiusmod tempor incididunt ut labore et dolore magna aliqua. Ut enim ad minim veniam, quis nostrud exercitation.
        Lorem ipsum dolor sit amet, consectetur adipisicing elit, sed do eiusmod tempor incididunt ut labore et dolore magna aliqua. Ut enim ad minim veniam, quis nostrud exercitation.
        Lorem ipsum dolor sit amet, consectetur adipisicing elit, sed do eiusmod tempor incididunt ut labore et dolore magna aliqua. Ut enim ad minim veniam, quis nostrud exercitation.
      </p>
      <div class="back-boxes">
        <div class="placeholder-box">Logo</div>
        <div class="placeholder-box">ISBN</div>
      </div>
    </section>

    <section class="spine">
      <div class="spine__glow"></div>
      <div class="spine-text">
        <span class="spine-title">Brindle A Wyrm Chronicle</span>
        <span class="spine-author">Delphine Voss Marlowe</span>
      </div>
    </section>

    <section class="front-cover">
      <div class="front-art" role="img" aria-label="Illustration of a pale blue scaled dragon with dark horns and green crest, its coiled neck set against swirling orange and purple feathers"></div>
      <div class="front-type">
        <p class="front-series">Tales of the Meridian</p>
        <h1 class="front-title">
          <span class="front-title__line">Brindle</span>
          <span class="front-connector">
            <span class="wings-ornament" role="img" aria-label="Pair of white feathered wings ornament"></span>
            <span class="front-connector__a">A</span>
          </span>
          <span class="front-title__line">Wyrm</span>
          <span class="front-title__line">Chronicle</span>
        </h1>
        <p class="front-author">Delphine Voss Marlowe</p>
      </div>
    </section>
  </main>
</body>
</html>
```